KTR Photography Editing & Support Services for Real Estate

We require a double sided A4 flyer to promote our photography services to real estate agencies.
This particular service is targeted to rural areas where reliable, professional and highly skilled photographers are difficult to source. We teach the agent how to photograph, they upload files to a server and we take care of the rest (image editing, quality control and delivery). This will give the agents flexibility with when to shoot and eliminates the stress of managing a photographer / contractor. We offer a 1 day face to face training session and competitive packages for equipment start up.
We would like the flyer to look clean & very professional. The flyer should showcase samples of our work to highlight what can be achieved by using our services. We like the look of a black or dark background behind the text and feel that would look nice with our photographs provided. Otherwise open to your suggestions and ideas.
TEXT FOR FLYER:
Welcome to the KTR Real Estate Photography Editing and Support Service
• Take your real estate business to the next level by providing impressive real estate imagery that makes you stands out from the competition
• Omit the stress of trying to find a good photographer or managing an unreliable one and hence have more time to focus on other aspects of your business
• Showcase your listings with better quality and more impactful photographs than your competitors thereby increasing potential for a quick sale
• Great first impressions matter and you will achieve this by looking and feeling more professional. This will attract and retain more future clients.
HOW IT WORKS
• We understand that your time is valuable, so let us handle the editing and delivery of your images. You shoot, and we take care of the rest.
• Images are edited and delivered within 1 working day
INCLUSIONS:
• Full day face to face training (we come to you) and instructional handbook
• We will teach you everything you need to know about your equipment and how to take stunning real estate photographs
• Service turnaround within 1 working day
• Free HELP desk service Mon-Fri
• 12 month Exclusivity (rural towns only) for a limited time
INVESTMENT
• 99 per listing for us to manage images including editing, quality control and delivery (10 Images)
• Ask us about competitive packages for photography equipment if required
SUMMARY
The KTR Real Estate Photography Editing and Support Service is the perfect solution for busy real estate professionals who want to take their business to the next level. Our service is affordable, flexible, and designed to help you showcase your listings in the best possible light.
Contact us today to learn more about how we can help you.

```html
<!DOCTYPE html>
<html lang="en">
<head>
<meta charset="utf-8">
<title>KTR Real Estate Photography Flyer</title>
<link href="https://fonts.googleapis.com/css2?family=Cormorant+Garamond:wght@500;600&family=Montserrat:wght@300;400&display=swap" rel="stylesheet">
<style>
  :root {
    --ink: #2a2a2a;
    --tan: #bcb097;
    --paper: #ffffff;
    --stage: #e9e7e3;
    --text-dark: #3a3a3a;
    --text-light: #f4f1ea;
  }
  * { box-sizing: border-box; margin: 0; padding: 0; }
  html, body { width: 1200px; height: 900px; overflow: hidden; }
  body { background: var(--stage); position: relative; font-family: "Montserrat", sans-serif; }

  .flyer {
    position: absolute; top: 61px; width: 550px; height: 778px;
    background: var(--paper); overflow: hidden;
    box-shadow: 0 6px 18px rgba(0,0,0,.18);
  }
  .flyer--front { left: 40px; }
  .flyer--back { left: 610px; }

  .masthead {
    position: absolute; left: 0; top: 0; width: 100%; height: 95px; background: var(--ink);
    display: flex; align-items: center; justify-content: center; gap: 14px;
  }
  .masthead__mark { width: 10px; height: 10px; background: var(--text-light); }
  .masthead__name {
    color: var(--text-light); font-weight: 300; font-size: 17px; letter-spacing: 5px; text-transform: uppercase;
  }
  .masthead__rule {
    position: absolute; left: 0; top: 86px; width: 290px; height: 9px; background: var(--tan);
    clip-path: polygon(0 0, 94% 0, 100% 100%, 0 100%);
  }

  .photo { position: absolute; }
  .hero { left: 0; top: 95px; width: 100%; height: 266px; }
  .hero--lounge { background: linear-gradient(160deg, #6b4a30 0%, #2e4a6e 40%, #7d5e45 70%, #3a3430 100%); }
  .hero--kitchen { background: linear-gradient(180deg, #f2f0ec 0%, #e6e1d9 55%, #b59470 85%, #8c6c4e 100%); }

  .panel { position: absolute; left: 0; background: var(--tan); border-top-right-radius: 12px; }
  .panel--welcome { top: 328px; width: 219px; height: 233px; padding: 24px 10px 0 17px; color: var(--text-light); }
  .panel--inclusions { top: 348px; width: 222px; height: 328px; padding: 20px 10px 0 10px; color: var(--text-light); }

  .welcome__lead { font-family: "Cormorant Garamond", serif; font-size: 14px; color: var(--ink); font-weight: 500; }
  .welcome__title { font-family: "Cormorant Garamond", serif; font-size: 18px; line-height: 1.15; color: var(--ink); font-weight: 500; text-transform: uppercase; margin-top: 2px; }
  .welcome__sub { font-family: "Cormorant Garamond", serif; font-size: 14px; color: var(--ink); font-weight: 500; }
  .welcome__rule { width: 56px; height: 2px; background: var(--ink); margin: 10px 0 14px; }
  .panel p { font-size: 8.3px; line-height: 1.3; font-weight: 400; text-align: justify; margin-bottom: 10px; }

  .section-title { font-family: "Cormorant Garamond", serif; font-size: 18px; color: var(--ink); font-weight: 500; text-transform: uppercase; margin-bottom: 12px; }
  .section-title--spaced { margin-top: 20px; }
  .points { list-style: none; }
  .points li { font-size: 8.3px; line-height: 1.3; margin-bottom: 9px; }
  .points li::before { content: "• "; }
  .panel .points li { margin-bottom: 7px; }

  .benefits { position: absolute; left: 233px; top: 389px; width: 301px; color: var(--text-dark); }
  .benefits li { text-align: justify; margin-bottom: 10px; }

  .thumbs { position: absolute; left: 16px; top: 571px; width: 518px; height: 105px; display: flex; gap: 4px; }
  .thumbs .photo { position: static; flex: 1; border: 2px solid #fff; }
  .band { position: absolute; left: 0; top: 652px; width: 100%; height: 126px; background: var(--ink); }
  .thumbs { z-index: 2; }
  .band--back { top: 676px; height: 102px; }

  .cta {
    position: absolute; left: 0; width: 100%; text-align: center; color: var(--text-light);
    font-family: "Cormorant Garamond", serif; font-size: 15px; font-weight: 500; text-transform: uppercase; letter-spacing: .3px;
  }
  .flyer--front .cta { top: 703px; }
  .flyer--back .cta { top: 707px; }
  .contact-pill {
    position: absolute; left: 112px; width: 328px; height: 19px; border-radius: 10px; background: var(--tan);
    display: flex; align-items: center; justify-content: center; gap: 14px;
    color: var(--text-light); font-size: 7.6px;
  }
  .flyer--front .contact-pill { top: 740px; }
  .flyer--back .contact-pill { top: 744px; }
  .contact-pill span { display: inline-flex; align-items: center; gap: 5px; }
  .contact-pill svg { width: 8px; height: 8px; }

  .how { position: absolute; left: 233px; top: 382px; width: 309px; text-align: right; color: var(--text-dark); }
  .how .section-title { margin-bottom: 6px; }
  .how p { font-size: 8.3px; line-height: 1.3; }
  .gallery { position: absolute; left: 234px; top: 446px; width: 308px; height: 230px; display: grid; grid-template-columns: 1fr 1fr; gap: 8px; z-index: 2; }
  .gallery .photo { position: static; border: 2px solid #fff; }
</style>
</head>
<body>

<article class="flyer flyer--front">
  <header class="masthead">
    <span class="masthead__mark"></span>
    <span class="masthead__name">Kurt Rayner Photographer</span>
    <span class="masthead__rule"></span>
  </header>
  <div class="photo hero hero--lounge" role="img" aria-label="Timber-lined living room with tall windows at dusk and a hanging fireplace"></div>

  <section class="panel panel--welcome">
    <div class="welcome__lead">Welcome to</div>
    <h1 class="welcome__title">The KTR Real Estate Photography</h1>
    <div class="welcome__sub">Editing and Support Service</div>
    <div class="welcome__rule"></div>
    <p>The KTR Real Estate Photography Editing and Support Service is the perfect solution for busy real estate professionals who want to take their business to the next level.</p>
    <p>Our service is affordable, flexible, and designed to help you showcase your listings in the best possible light.</p>
  </section>

  <ul class="points benefits">
    <li>Take your real estate business to the next level by providing impressive real estate imagery that makes you stands out from the competition</li>
    <li>Omit the stress of trying to find a good photographer or managing an unreliable one and hence have more time to focus on other aspects of your business</li>
    <li>Showcase your listings with better quality and more impactful photographs than your competitors thereby increasing potential for a quick sale</li>
    <li>Great first impressions matter and you will achieve this by looking and feeling more professional. This will attract and retain more future clients.</li>
  </ul>

  <div class="band"></div>
  <div class="thumbs">
    <div class="photo" style="background:linear-gradient(135deg,#8a6a4c,#d9d4cc)" role="img" aria-label="Hallway with timber floor and framed art"></div>
    <div class="photo" style="background:linear-gradient(135deg,#e8e6e2,#7f8a78)" role="img" aria-label="Bright bedroom opening to a rural view"></div>
    <div class="photo" style="background:linear-gradient(135deg,#d8d2c8,#b9ad9c)" role="img" aria-label="Stone bathroom with freestanding bath"></div>
    <div class="photo" style="background:linear-gradient(180deg,#7f89a6,#c9b9a3 60%,#6d6e5f)" role="img" aria-label="Gabled farmhouse exterior at dusk"></div>
  </div>
  <div class="cta">Contact us today to learn more about how we can help you.</div>
  <div class="contact-pill">
    <span>Contact Us NOW!</span>
    <span><svg viewBox="0 0 10 10"><circle cx="5" cy="5" r="5" fill="#2a2a2a"/><path d="M3.2 2.6l1 1-.5.6a3 3 0 0 0 1.7 1.7l.6-.5 1 1-.7.8C4.6 7 3 5.4 2.4 3.3z" fill="#f4f1ea"/></svg>0400 555 218</span>
    <span><svg viewBox="0 0 10 10"><circle cx="5" cy="5" r="5" fill="#2a2a2a"/><rect x="2.5" y="3.3" width="5" height="3.4" fill="none" stroke="#f4f1ea" stroke-width=".7"/><path d="M2.5 3.3L5 5.3l2.5-2" fill="none" stroke="#f4f1ea" stroke-width=".7"/></svg>info@kurtrayner.com.au</span>
  </div>
</article>

<article class="flyer flyer--back">
  <header class="masthead">
    <span class="masthead__mark"></span>
    <span class="masthead__name">Kurt Rayner Photographer</span>
    <span class="masthead__rule"></span>
  </header>
  <div class="photo hero hero--kitchen" role="img" aria-label="White open-plan kitchen and dining room with dark timber beams"></div>

  <section class="panel panel--inclusions">
    <h2 class="section-title">Inclusions</h2>
    <ul class="points">
      <li>Full day face to face training (we come to you) and instructional handbook</li>
      <li>We will teach you everything you need to know about your equipment and how to take stunning real estate photographs</li>
      <li>Service turnaround within 1 working day</li>
      <li>Free HELP desk service Mon-Fri</li>
      <li>12 month Exclusivity (rural towns only) for a limited time</li>
    </ul>
    <h2 class="section-title section-title--spaced">Investment</h2>
    <ul class="points">
      <li>99 per listing for us to manage images including editing, quality control and delivery (10 Images)</li>
      <li>Ask us about competitive packages for photography equipment if required</li>
    </ul>
  </section>

  <section class="how">
    <h2 class="section-title">How it works</h2>
    <p>We understand that your time is valuable, so let us handle the editing and delivery of your images. You shoot, and we take care of the rest. Images are edited and delivered within 1 working day</p>
  </section>

  <div class="band band--back"></div>
  <div class="gallery">
    <div class="photo" style="background:linear-gradient(135deg,#3d4650,#1f2226)" role="img" aria-label="Dark lounge with leather sofa"></div>
    <div class="photo" style="background:linear-gradient(180deg,#9fb3c9,#3b3d3f 60%,#7a8a5a)" role="img" aria-label="Dark cottage exterior with garden path"></div>
    <div class="photo" style="background:linear-gradient(180deg,#c9b8b0,#5d7488 55%,#4f6a3a)" role="img" aria-label="Black cabin on a clifftop overlooking the sea"></div>
    <div class="photo" style="background:linear-gradient(160deg,#e8ecef,#a4886a 70%,#6e8a5c)" role="img" aria-label="Timber deck with outdoor furniture and view"></div>
  </div>
  <div class="cta">Contact us today to learn more about how we can help you.</div>
  <div class="contact-pill">
    <span>Contact Us NOW!</span>
    <span><svg viewBox="0 0 10 10"><circle cx="5" cy="5" r="5" fill="#2a2a2a"/><path d="M3.2 2.6l1 1-.5.6a3 3 0 0 0 1.7 1.7l.6-.5 1 1-.7.8C4.6 7 3 5.4 2.4 3.3z" fill="#f4f1ea"/></svg>0400 555 218</span>
    <span><svg viewBox="0 0 10 10"><circle cx="5" cy="5" r="5" fill="#2a2a2a"/><rect x="2.5" y="3.3" width="5" height="3.4" fill="none" stroke="#f4f1ea" stroke-width=".7"/><path d="M2.5 3.3L5 5.3l2.5-2" fill="none" stroke="#f4f1ea" stroke-width=".7"/></svg>info@kurtrayner.com.au</span>
  </div>
</article>

</body>
</html>
```